Website redesign for KestrelFinanceMan/TKFinanceMan

Job Title: Talented Web Designer for SEO-Friendly Website Creation & HostFalcon cPanel Integration
 
Inspiration: dunewheelracingexample.com
Pages:

About
Get a Quote
FAQ
Boat Loans
RV Loans
Testimonials
News/Blog
Affiliate Program
Contact

Job Description:
 
We are seeking a skilled and creative freelance web designer to build a stunning, SEO-optimized website for our business. The ideal candidate will have a strong design portfolio, technical expertise in creating search engine-friendly websites, and experience implementing websites into HostFalcon cPanel.
 
Project Overview:
 
Objective: Create a modern, motorsports themed visually appealing website that is optimized for SEO.

Platform: The site will be hosted on HostFalcon, so familiarity with their cPanel for setup and integration is essential.

Deliverables:
         •A fully functional website (desktop and mobile) with user-friendly navigation and a responsive design.
         •SEO best practices implemented throughout, including proper meta tags, optimized images, fast loading speeds, and mobile compatibility.
         •Seamless integration into HostFalcon cPanel for hosting.
         •Guidance or documentation on maintaining the site post-launch.
 
Key Skills Required:
 
         •Proficiency in web design (HTML, CSS, JavaScript, or relevant platforms like WordPress).
         •Knowledge of SEO principles and tools for website optimization.
         •Experience with HostFalcon cPanel, including file management and DNS settings.
         •Strong communication skills to understand our vision and provide progress updates.
 
What We’re Looking For:
 
         •A designer who can transform our ideas into a sleek and functional website.
         •Someone proactive in suggesting creative design elements and SEO improvements.
         •A reliable professional who can meet deadlines and deliver a polished product.
 
Please provide:
 
         1.A brief introduction and why you’re a good fit for this project.
         2.Examples of previous web design projects, especially those with SEO implementation.
         3.Your estimated timeline and cost for this project.
 
We are excited to work with a talented designer who can bring our vision to life. If you are passionate about web design and SEO, we’d love to hear from you!

Target Market(s)

Boat and RV buyers looking for a loan

Coding

Coded - Design and coding required

Number of Pages Required

5+ page

Colors
F0912C
F2A743
F7CA91
FBE8D2
FDF5EE

Requirements
Must have
• motorsports type design
Nice to have
• fcontact forms easy to use layout on brand and color scheme of kestrelfinanceman and tkfinanceman.example

```html
<!DOCTYPE html>
<html lang="en">
<head>
<meta charset="utf-8">
<title>TKFinanceMan – RV Loans Made Easy</title>
<link href="https://fonts.googleapis.com/css2?family=Saira:wght@700;800&family=Roboto:wght@400;500;700&display=swap" rel="stylesheet">
<style>
:root{
  --orange:#e2621b;
  --orange-bright:#f26a1b;
  --orange-deep:#c4520f;
  --blue:#1e88e5;
  --ink:#1f1f1f;
  --dark:#1c1c1c;
  --grey:#555;
  --muted:#7a7a7a;
  --peach:#fdf5ee;
  --white:#fff;
}
*{box-sizing:border-box;margin:0;padding:0}
html,body{width:1200px;height:4971px;overflow:hidden}
body{font-family:"Roboto",Arial,sans-serif;color:var(--ink);background:var(--white);position:relative}
section,header,footer{position:absolute;left:0;width:1200px;overflow:hidden}
.edge-line{position:absolute;left:0;width:1200px;height:6px;background:var(--orange-deep)}

/* header */
.site-header{top:0;height:100px;background:var(--white)}
.topbar{position:absolute;left:506px;top:0;width:694px;height:40px;background:var(--orange-bright);clip-path:polygon(18px 0,100% 0,100% 100%,0 100%);display:flex;align-items:center;color:#fff;font-size:12.5px;padding-left:54px;gap:30px}
.topbar .social{display:flex;gap:8px;margin-left:auto;margin-right:112px}
.topbar .social span{width:26px;height:26px;border:1.5px solid #fff;border-radius:50%;display:block}
.brand{position:absolute;display:flex;align-items:center;gap:8px;font-family:"Roboto",sans-serif;font-weight:700;font-size:26px;line-height:30px;color:var(--orange)}
.brand i{width:22px;height:22px;border-radius:50%;background:var(--orange);display:block}
.main-nav{position:absolute;left:418px;top:62px;display:flex;gap:18px;font-size:13px;font-weight:500;color:#222}
.quote-btn{position:absolute;left:945px;top:54px;width:142px;height:36px;background:#4a4a4a;color:#fff;font-weight:500;font-size:14px;display:flex;align-items:center;justify-content:center;clip-path:polygon(10px 0,100% 0,calc(100% - 10px) 100%,0 100%)}

/* buttons */
.btn{position:absolute;display:flex;align-items:center;justify-content:center;font-weight:700;font-size:15px;letter-spacing:.5px;clip-path:polygon(16px 0,100% 0,calc(100% - 16px) 100%,0 100%)}
.btn-orange{background:var(--orange-bright);color:#fff}
.btn-white{background:#fff;color:var(--orange)}
.btn-grey{background:#5a5a5a;color:#fff}

/* section title */
.sec-title{position:absolute;left:0;width:1200px;display:flex;justify-content:center;align-items:center;font-family:"Saira",sans-serif;font-weight:800;font-size:33px;letter-spacing:.5px;color:var(--ink)}
.sec-title.light{color:#fff}
.sec-title .badge{background:var(--blue);color:#fff;padding:0 12px;margin-right:10px;line-height:44px;clip-path:polygon(8px 0,100% 0,calc(100% - 8px) 100%,0 100%)}

/* hero */
.hero{top:100px;height:560px;background:linear-gradient(120deg,#151515 0%,#2b2b2b 55%,#3c3c3c 100%)}
.hero h1{position:absolute;left:110px;top:96px;font-family:"Saira",sans-serif;font-weight:800;font-size:50px;line-height:60px;color:#fff}
.hero h1 em{font-style:normal;color:var(--orange-bright)}
.hero p{position:absolute;left:112px;top:238px;width:360px;font-size:16px;line-height:27px;color:#fff}
.hero-photo{position:absolute;left:520px;top:40px;width:680px;height:520px;background:radial-gradient(ellipse at 55% 55%,#e8e8e8 0%,#b9b9b9 40%,rgba(60,60,60,0) 70%)}

/* categories */
.types{top:660px;height:605px}
.type-card{position:absolute;top:180px;width:240px;text-align:center}
.type-card .photo{height:175px;clip-path:polygon(4% 0,100% 0,96% 100%,0 100%)}
.type-card h3{font-size:17px;font-weight:700;margin-top:18px}
.type-card .grass{height:30px;margin-top:10px;background:linear-gradient(90deg,#3c5a1e,#7c9a35 40%,#a8a249 70%,#4d3a1c);clip-path:polygon(3% 0,100% 0,97% 100%,0 100%)}

/* about */
.about{top:1265px;height:665px;background:linear-gradient(180deg,#d4601c,#c4520f)}
.about-photo{position:absolute;left:0;top:115px;width:600px;height:430px;background:linear-gradient(135deg,#8a8a8a,#dcdcdc 45%,#6d6d6d)}
.about h3{position:absolute;left:670px;top:230px;font-size:17px;font-weight:500;color:#fff}
.checks{position:absolute;left:670px;top:267px;width:460px;display:grid;grid-template-columns:230px 230px;row-gap:10px;font-size:13px;color:#fff}
.checks li{list-style:none;display:flex;align-items:center;gap:8px}
.checks svg{width:14px;height:14px;flex:none}
.about p{position:absolute;left:670px;top:372px;width:440px;font-size:13.5px;line-height:25px;color:#fff}

/* services */
.services{top:1930px;height:660px}
.services .lead{position:absolute;top:148px;width:1200px;text-align:center;font-size:13.5px;color:var(--grey)}
.service{position:absolute;top:225px;width:335px;height:365px;text-align:center;padding-top:40px}
.service.featured{background:#fff;border-radius:22px;box-shadow:0 6px 24px rgba(0,0,0,.13);border-bottom:6px solid var(--orange)}
.service .icon{width:116px;height:116px;border-radius:50%;background:var(--grey);margin:0 auto;display:flex;align-items:center;justify-content:center}
.service.featured .icon{background:var(--orange-deep)}
.service h3{font-size:17px;font-weight:700;margin-top:36px}
.service p{font-size:13.5px;line-height:24px;color:var(--muted);width:270px;margin:14px auto 0}
.read-more{display:inline-flex;align-items:center;gap:6px;color:var(--orange-deep);font-size:13px;font-weight:700;margin-top:20px}
.read-more b{width:12px;height:12px;border-radius:50%;background:var(--orange-deep);display:inline-block;position:relative}
.read-more b::after{content:"";position:absolute;left:4px;top:3px;border:3px solid transparent;border-left:5px solid #fff}

/* testimonials */
.testimonials{top:2590px;height:550px;background:linear-gradient(180deg,#d4601c,#c0500e)}
.testimonials-photo{position:absolute;left:850px;top:10px;width:310px;height:150px;background:linear-gradient(135deg,#cfcfcf,#f4f4f4 50%,#8d8d8d);border-radius:18px}
.quote-card{position:absolute;top:225px;width:407px;height:230px;background:#fff;border-radius:24px}
.avatar{position:absolute;left:-50px;top:55px;width:116px;height:116px;border-radius:50%;background:linear-gradient(135deg,#8a6a52,#d8b89a);border:4px solid #fff}
.quote-card .qm{position:absolute;left:100px;top:22px;font-family:"Saira",sans-serif;font-size:58px;color:var(--orange);line-height:1}
.quote-card p{position:absolute;left:100px;top:78px;width:275px;font-size:13.5px;line-height:24px;color:var(--muted)}
.quote-card h4{position:absolute;left:100px;top:163px;font-size:15px;font-weight:700}
.quote-card .stars{position:absolute;left:100px;top:183px;color:var(--orange);font-size:15px;letter-spacing:2px}
.arrow{position:absolute;width:22px;height:22px;border-left:4px solid #fff;border-bottom:4px solid #fff}

/* partners */
.partners{top:3140px;height:330px;background:var(--peach)}
.partner{position:absolute;top:178px;width:168px;height:84px;background:#fff;border-radius:6px;box-shadow:0 2px 10px rgba(0,0,0,.08);display:flex;align-items:center;justify-content:center}
.partner span{display:block;width:100px;height:28px;border-radius:4px}
.chev{position:absolute;top:208px;width:20px;height:20px;border-left:2px solid #555;border-bottom:2px solid #555}

/* news */
.news{top:3470px;height:630px}
.post{position:absolute;top:178px;width:307px;height:412px;background:#fff;box-shadow:0 2px 12px rgba(0,0,0,.1)}
.post .photo{height:212px;position:relative}
.post .date{position:absolute;right:0;bottom:0;background:var(--blue);color:#fff;font-size:12px;padding:5px 14px}
.post h3{font-size:16.5px;line-height:24px;font-weight:700;margin:20px 16px 0}
.post p{font-size:13px;line-height:21px;color:var(--muted);margin:12px 16px 0}
.post .more{display:block;margin:12px 16px 0;font-size:13px;font-weight:700;color:var(--orange-deep)}

/* loan calculator */
.calculator{top:4100px;height:500px;background:linear-gradient(180deg,#d4601c,#c0500e)}
.calculator-photo{position:absolute;left:40px;top:20px;width:320px;height:180px;background:linear-gradient(135deg,#bdbdbd,#f2f2f2 50%,#7a7a7a);border-radius:12px}
.field{position:absolute;top:245px;height:46px;background:#fff;font-size:13px;color:#999;padding:14px 14px}

/* footer */
.site-footer{top:4600px;height:371px;background:var(--dark);color:#fff}
.site-footer .brand{left:112px;top:160px;color:#fff;font-size:24px}
.foot-social{position:absolute;left:172px;top:212px;display:flex;gap:11px}
.foot-social span{width:28px;height:28px;border-radius:50%;background:#fff}
.foot-social span.on{background:var(--orange)}
.foot-col{position:absolute;top:50px}
.foot-col h4{font-size:15px;font-weight:700;margin-bottom:18px}
.foot-col li{list-style:none;font-size:12.5px;line-height:26px}
.contact-item{display:flex;gap:10px;margin-bottom:14px;font-size:12.5px;line-height:17px}
.contact-item b{display:block;font-size:11.5px}
.contact-item svg{flex:none;margin-top:2px}
.to-top{position:absolute;left:1134px;top:200px;width:34px;height:34px;border-radius:50%;background:var(--orange);display:flex;align-items:center;justify-content:center}
.copyright{position:absolute;top:320px;width:1200px;text-align:center;font-size:13px}
</style>
</head>
<body>
<svg width="0" height="0" style="position:absolute" aria-hidden="true">
  <defs>
    <symbol id="tick" viewBox="0 0 14 14">
      <circle cx="7" cy="7" r="7" fill="#fff"/>
      <path d="M3.8 7.2 L6 9.3 L10.2 4.9" fill="none" stroke="#c4520f" stroke-width="1.8"/>
    </symbol>
  </defs>
</svg>

<header class="site-header">
  <div class="topbar">
    <span>✉ dana@tkfinanceman.example</span>
    <span>☎ Call US Today : 555-014-2290</span>
    <div class="social"><span></span><span></span><span></span></div>
  </div>
  <div class="brand" style="left:115px;top:30px"><i></i>TKFinanceMan</div>
  <nav class="main-nav">
    <span>About</span><span>RV Loans</span><span>FAQ</span><span>Testimonials</span><span>News</span><span>Affiliate Program</span><span>Contact</span>
  </nav>
  <div class="quote-btn">Get a Quote</div>
</header>

<section class="hero">
  <div class="hero-photo" role="img" aria-label="White Class C motorhome on a dark background"></div>
  <h1><em>RV LOANS</em> MADE<br>EASY!</h1>
  <p>Welcome to TKFinanceMan.com, your one-stop resource for all of your RV financing needs.</p>
  <div class="btn btn-orange" style="left:112px;top:328px;width:250px;height:50px">APPLY TODAY</div>
  <div class="edge-line" style="bottom:0"></div>
</section>

<section class="types">
  <h2 class="sec-title" style="top:70px"><span class="badge">WE FINANCE</span>ALL TYPES OF RV'S</h2>
  <div class="type-card" style="left:92px">
    <div class="photo" role="img" aria-label="Diesel pusher motorhome on a mountain road" style="background:linear-gradient(160deg,#9fb1c4,#e9e9e9 50%,#6b6f5a)"></div>
    <h3>Diesel Pushers</h3><div class="grass"></div>
  </div>
  <div class="type-card" style="left:352px">
    <div class="photo" role="img" aria-label="Class A motorhome parked among pine trees" style="background:linear-gradient(160deg,#3d5a3a,#dcdcdc 55%,#4d5c3a)"></div>
    <h3>Class A</h3><div class="grass"></div>
  </div>
  <div class="type-card" style="left:612px">
    <div class="photo" role="img" aria-label="Class B camper trailer at sunset by a lake" style="background:linear-gradient(160deg,#3a5f8c,#e39a4c 50%,#4a3a2a)"></div>
    <h3>Class b</h3><div class="grass"></div>
  </div>
  <div class="type-card" style="left:872px">
    <div class="photo" role="img" aria-label="Class C motorhome beside the sea" style="background:linear-gradient(160deg,#8ec5e8,#e8e3d6 55%,#c9b38a)"></div>
    <h3>Class c</h3><div class="grass"></div>
  </div>
  <div class="btn btn-orange" style="left:492px;top:488px;width:216px;height:48px">APPLY NOW</div>
</section>

<section class="about">
  <div class="about-photo" role="img" aria-label="Silver Class A coach motorhome"></div>
  <h2 class="sec-title light" style="left:670px;top:132px;width:auto"><span class="badge">ABOUT</span>US</h2>
  <h3>Your trusted source for RV Financing.</h3>
  <ul class="checks">
    <li><svg><use href="#tick"/></svg>Loans from $25,000 - $5M</li>
    <li><svg><use href="#tick"/></svg>Quick Funding</li>
    <li><svg><use href="#tick"/></svg>Up to 25yrs old</li>
    <li><svg><use href="#tick"/></svg>Private Party or Dealer</li>
    <li><svg><use href="#tick"/></svg>Same-Day Approvals</li>
    <li><svg><use href="#tick"/></svg>Best Rates in the Industry</li>
  </ul>
  <p>Our goal is to make your RV purchase as quick and stress-free as possible. Our numerous lender relationships allow us to offer competitive rates and terms with quick turn-around times.</p>
  <div class="btn btn-white" style="left:672px;top:490px;width:190px;height:50px">LEARN MORE</div>
</section>

<section class="services">
  <h2 class="sec-title" style="top:82px"><span class="badge">WE FINANCE</span>MORE THAN JUST BOATS</h2>
  <p class="lead">At Summit Recreational Finance, we are your one-stop resource for all marine, RV and Airplane Financing</p>
  <div class="service" style="left:86px">
    <div class="icon"><svg width="60" height="60" viewBox="0 0 60 60" fill="none" stroke="#fff" stroke-width="2.5"><path d="M8 36 L52 36 L46 48 L14 48 Z"/><path d="M16 36 V26 H44 V36"/><path d="M22 26 V18 H36 V26"/><path d="M28 18 V10"/><path d="M6 54 Q12 50 18 54 T30 54 T42 54 T54 54"/></svg></div>
    <h3>Marine Financing</h3>
    <p>Lorem ipsum dolor sit amet, consectetur adipiscing elit, sed do eiusmod tempor labore et dolore magna aliqua.</p>
    <span class="read-more">READ MORE <b></b></span>
  </div>
  <div class="service featured" style="left:433px">
    <div class="icon"><svg width="62" height="60" viewBox="0 0 62 60" fill="none" stroke="#fff" stroke-width="2.5"><rect x="6" y="16" width="40" height="28" rx="2"/><path d="M46 24 H52 L58 34 V44 H46"/><rect x="12" y="22" width="10" height="8"/><rect x="26" y="22" width="12" height="8"/><circle cx="16" cy="46" r="5"/><circle cx="48" cy="46" r="5"/></svg></div>
    <h3>RV Financing</h3>
    <p>Lorem ipsum dolor sit amet, consectetur adipiscing elit, sed do eiusmod tempor labore et dolore magna aliqua.</p>
    <span class="read-more">READ MORE <b></b></span>
  </div>
  <div class="service" style="left:780px">
    <div class="icon"><svg width="62" height="60" viewBox="0 0 62 60" fill="none" stroke="#fff" stroke-width="2.5"><path d="M6 30 L52 26 Q58 28 52 32 L6 34 Z"/><path d="M28 28 L20 12 H26 L38 27"/><path d="M28 33 L20 48 H26 L38 33"/><path d="M8 30 L4 22 H9 L14 29"/></svg></div>
    <h3>Aircraft Financing</h3>
    <p>Lorem ipsum dolor sit amet, consectetur adipiscing elit, sed do eiusmod tempor labore et dolore magna aliqua.</p>
    <span class="read-more">READ MORE <b></b></span>
  </div>
</section>

<section class="testimonials">
  <div class="testimonials-photo" role="img" aria-label="White Class C motorhome"></div>
  <h2 class="sec-title light" style="top:160px"><span class="badge">WHAT OUR</span>CUSTOMERS SAY</h2>
  <div class="arrow" style="left:50px;top:330px;transform:rotate(45deg)"></div>
  <div class="arrow" style="left:1128px;top:330px;transform:rotate(-135deg)"></div>
  <div class="quote-card" style="left:165px">
    <div class="avatar" role="img" aria-label="Customer portrait"></div>
    <div class="qm">“</div>
    <p>Lorem ipsum dolor sit amet, consectetur adipiscing elit, sed do eiusmod tempor incididunt ut magna aliqua.</p>
    <h4>John Doe</h4><div class="stars">★★★★★</div>
  </div>
  <div class="quote-card" style="left:680px">
    <div class="avatar" role="img" aria-label="Customer portrait"></div>
    <div class="qm">“</div>
    <p>Lorem ipsum dolor sit amet, consectetur adipiscing elit, sed do eiusmod tempor incididunt ut magna aliqua.</p>
    <h4>John Doe</h4><div class="stars">★★★★★</div>
  </div>
</section>

<section class="partners">
  <h2 class="sec-title" style="top:70px"><span class="badge">OUR</span>PARTNERS</h2>
  <div class="chev" style="left:60px;transform:rotate(45deg)"></div>
  <div class="chev" style="left:1120px;transform:rotate(-135deg)"></div>
  <div class="partner" style="left:118px"><span style="background:#c9d3e6"></span></div>
  <div class="partner" style="left:318px"><span style="background:#d63a2f"></span></div>
  <div class="partner" style="left:516px"><span style="background:#8aa0c8"></span></div>
  <div class="partner" style="left:716px"><span style="background:#9a9a9a"></span></div>
  <div class="partner" style="left:914px"><span style="background:#5a5a5a"></span></div>
</section>

<section class="news">
  <h2 class="sec-title" style="top:88px"><span class="badge">OUR</span>LATEST NEWS</h2>
  <article class="post" style="left:112px">
    <div class="photo" role="img" aria-label="Pickup truck towing a fifth-wheel trailer" style="background:linear-gradient(170deg,#6fa3d6,#dfe6ec 55%,#6d6d6d)"><span class="date">Aug 24, 2024</span></div>
    <h3>Lorem ipsum dolor sit amet consectetur adipiscing elit, sed do</h3>
    <p>Sed ut perspiciatis unde omnis iste natus beatae vitae dicta sunt explicabo.</p>
    <span class="more">READ MORE ›</span>
  </article>
  <article class="post" style="left:446px">
    <div class="photo" role="img" aria-label="Pickup truck towing a boat on a trailer" style="background:linear-gradient(170deg,#b9c7d3,#e6e6e6 55%,#8a8a8a)"><span class="date">Aug 24, 2024</span></div>
    <h3>Lorem ipsum dolor sit amet consectetur adipiscing elit, sed do</h3>
    <p>Sed ut perspiciatis unde omnis iste natus beatae vitae dicta sunt explicabo.</p>
    <span class="more">READ MORE ›</span>
  </article>
  <article class="post" style="left:780px">
    <div class="photo" role="img" aria-label="Motorhome in a green mountain valley" style="background:linear-gradient(170deg,#8fb4d8,#a8b0a0 45%,#5f7d3e)"><span class="date">Aug 24, 2024</span></div>
    <h3>Lorem ipsum dolor sit amet consectetur adipiscing elit, sed do</h3>
    <p>Sed ut perspiciatis unde omnis iste natus beatae vitae dicta sunt explicabo.</p>
    <span class="more">READ MORE ›</span>
  </article>
</section>

<section class="calculator">
  <div class="calculator-photo" role="img" aria-label="White fifth-wheel travel trailer"></div>
  <h2 class="sec-title light" style="top:150px"><span class="badge">LOAN</span>CALCULATION</h2>
  <div class="field" style="left:112px;width:314px">Loan Amount</div>
  <div class="field" style="left:456px;width:302px">Loan Amount</div>
  <div class="field" style="left:774px;width:314px">Loan Amount</div>
  <div class="btn btn-grey" style="left:502px;top:340px;width:196px;height:48px;font-size:14px">SUBMIT NOW</div>
</section>

<footer class="site-footer">
  <div class="brand"><i></i>TKFinanceMan</div>
  <div class="foot-social"><span></span><span class="on"></span><span></span><span></span></div>
  <div class="foot-col" style="left:462px">
    <h4>Quick Links</h4>
    <ul><li>About</li><li>RV Loans</li><li>FAQ</li><li>Testimonials</li><li>News</li><li>Affiliate Program</li></ul>
  </div>
  <div class="foot-col" style="left:664px">
    <h4>About Company</h4>
    <ul><li>Privacy Policy</li><li>Cookie Policy</li><li>Terms &amp; Condition</li><li>Support</li><li>Contact</li><li>Site Map</li></ul>
  </div>
  <div class="foot-col" style="left:850px">
    <h4>Contact Us</h4>
    <div class="contact-item"><svg width="12" height="16" viewBox="0 0 12 16"><path d="M6 0 A6 6 0 0 1 12 6 C12 10 6 16 6 16 C6 16 0 10 0 6 A6 6 0 0 1 6 0 Z" fill="#e2621b"/><circle cx="6" cy="6" r="2.2" fill="#1c1c1c"/></svg><div><b>Location</b>4410 Harbor Ridge Road Ste. 210,<br>Bayview, CA 90000</div></div>
    <div class="contact-item"><svg width="14" height="14" viewBox="0 0 14 14"><path d="M3 0 L5.5 3.5 L4 5 Q5.5 8.5 9 10 L10.5 8.5 L14 11 L12 14 Q2 13 0 2 Z" fill="#e2621b"/></svg><div><b>Phone</b>(555) 014-2290</div></div>
    <div class="contact-item"><svg width="14" height="12" viewBox="0 0 14 12"><rect width="14" height="12" rx="1" fill="#e2621b"/><path d="M1 1.5 L7 6.5 L13 1.5" fill="none" stroke="#1c1c1c" stroke-width="1.3"/></svg><div><b>Email</b>dana@kestrelfinanceman.example</div></div>
  </div>
  <div class="to-top"><svg width="14" height="10" viewBox="0 0 14 10"><path d="M1 8 L7 2 L13 8" fill="none" stroke="#fff" stroke-width="2.5"/></svg></div>
  <p class="copyright">2024 Copyright - TKFinanceMan | All Rights Reserved</p>
</footer>
</body>
</html>
```